Packaging design for a reclosable bag for our product

We have a logo, and we need to put it on packaging for our product and while we want the look to be simple, we want it to follow good design principles and also contain spaces for other product descriptions.

There will be 5 sizes at launch so I'd like 5 variations, one for each size.

I've included a few mockups of the type of bag that I made but they are all just rough ideas that I had.

I want the brand to look scientific and methodical and even a bit quirky, as in "wow this is a serious product but also a bit unusual."

```html
<!DOCTYPE html>
<html lang="en">
<head>
<meta charset="utf-8">
<title>KN7 Bias Lighting – Pouch Front</title>
<link rel="stylesheet" href="https://fonts.googleapis.com/css2?family=Titillium+Web:wght@600;700&display=swap">
<style>
  :root {
    --backdrop: #c8c8c8;
    --pouch-black: #121212;
    --pouch-charcoal: #1d1d1d;
    --glow: rgba(255, 255, 255, 0.55);
    --white: #ffffff;
    --band-1: #f4f4f4;
    --band-2: #e3e3e3;
    --band-3: #d3d3d3;
    --band-4: #c2c2c2;
    --band-5: #b0b0b0;
    --band-6: #a0a0a0;
    --icon-fill: #1a1a1a;
    --ink: #1a1a1a;
  }
  * { margin: 0; padding: 0; box-sizing: border-box; }
  html, body {
    width: 1200px; height: 1200px; overflow: hidden;
    background: var(--backdrop);
  }
  .canvas {
    position: relative; width: 1200px; height: 1200px;
    background: var(--backdrop);
    font-family: "Titillium Web", "Arial Narrow", sans-serif;
  }
  .pouch {
    position: absolute; left: 266px; top: 168px;
    width: 668px; height: 866px;
    overflow: hidden;
    background: var(--band-6);
  }
  .pouch__header {
    position: absolute; left: 0; top: 0; width: 100%; height: 596px;
    background: linear-gradient(180deg, var(--pouch-charcoal) 0%, var(--pouch-black) 100%);
  }
  .pouch__zip {
    position: absolute; left: 0; top: 68px; width: 100%; height: 2px;
    background: rgba(255,255,255,0.12);
  }
  .brand-glow {
    position: absolute; left: 34px; top: 150px; width: 600px; height: 330px;
    background: radial-gradient(ellipse at center, var(--glow) 0%, rgba(255,255,255,0.18) 45%, rgba(255,255,255,0) 72%);
  }
  .brand-name {
    position: absolute; left: 0; top: 196px; width: 100%;
    text-align: center;
    font-weight: 700; font-size: 210px; line-height: 1;
    letter-spacing: -4px;
    color: var(--white);
  }
  .band { position: absolute; left: 0; width: 100%; }
  .band--subtitle { top: 596px; height: 54px; background: var(--white); }
  .band--1 { top: 650px; height: 46px; background: var(--band-1); }
  .band--2 { top: 696px; height: 48px; background: var(--band-2); }
  .band--3 { top: 744px; height: 40px; background: var(--band-3); }
  .band--4 { top: 784px; height: 38px; background: var(--band-4); }
  .band--5 { top: 822px; height: 44px; background: var(--band-5); }
  .product-title {
    position: absolute; left: 0; top: 532px; width: 100%;
    text-align: center;
    font-weight: 700; font-size: 66px; line-height: 1;
    color: var(--white);
    letter-spacing: 0.5px;
  }
  .product-subtitle {
    position: absolute; left: 0; top: 604px; width: 100%;
    text-align: center;
    font-weight: 600; font-size: 26px; line-height: 1.4;
    color: var(--ink);
    letter-spacing: 0.5px;
  }
  .spec-icons {
    position: absolute; left: 0; top: 670px; width: 100%;
    display: flex; justify-content: center; gap: 20px;
  }
  .spec-icon {
    width: 72px; height: 72px; border-radius: 9px;
    background: var(--icon-fill);
    display: flex; flex-direction: column; align-items: center; justify-content: flex-start;
    padding-top: 6px;
  }
  .spec-icon svg { width: 44px; height: 44px; display: block; }
  .spec-icon__label {
    color: var(--white); font-weight: 600; font-size: 13px; line-height: 1;
    margin-top: 3px; white-space: nowrap;
  }
</style>
</head>
<body>
<div class="canvas">
  <div class="pouch">
    <div class="pouch__header"></div>
    <div class="pouch__zip"></div>
    <div class="brand-glow"></div>
    <div class="brand-name">KN7</div>

    <div class="band band--subtitle"></div>
    <div class="band band--1"></div>
    <div class="band band--2"></div>
    <div class="band band--3"></div>
    <div class="band band--4"></div>
    <div class="band band--5"></div>

    <div class="product-title">BIAS LIGHTING</div>
    <div class="product-subtitle">6500K WHITE BIAS LIGHTING</div>

    <div class="spec-icons">
      <div class="spec-icon">
        <svg viewBox="0 0 44 44" aria-hidden="true">
          <circle cx="22" cy="22" r="11" fill="#fff"/>
          <text x="22" y="25" text-anchor="middle" font-family="Titillium Web, sans-serif" font-weight="700" font-size="8" fill="#1a1a1a">D65</text>
          <g stroke="#fff" stroke-width="1.6" stroke-linecap="round">
            <line x1="22" y1="3" x2="22" y2="7"/><line x1="22" y1="37" x2="22" y2="41"/>
            <line x1="3" y1="22" x2="7" y2="22"/><line x1="37" y1="22" x2="41" y2="22"/>
            <line x1="8.5" y1="8.5" x2="11.3" y2="11.3"/><line x1="32.7" y1="32.7" x2="35.5" y2="35.5"/>
            <line x1="35.5" y1="8.5" x2="32.7" y2="11.3"/><line x1="8.5" y1="35.5" x2="11.3" y2="32.7"/>
          </g>
        </svg>
        <span class="spec-icon__label">Simulated</span>
      </div>
      <div class="spec-icon">
        <svg viewBox="0 0 44 44" aria-hidden="true">
          <g fill="none" stroke="#fff" stroke-width="1.8">
            <circle cx="22" cy="22" r="18"/><circle cx="22" cy="22" r="13"/>
            <circle cx="22" cy="22" r="8"/><circle cx="22" cy="22" r="3"/>
          </g>
        </svg>
        <span class="spec-icon__label">Cable 5m</span>
      </div>
      <div class="spec-icon">
        <svg viewBox="0 0 44 44" aria-hidden="true">
          <circle cx="22" cy="22" r="18" fill="none" stroke="#fff" stroke-width="3" stroke-dasharray="3 2"/>
          <circle cx="22" cy="22" r="12" fill="#fff"/>
          <text x="22" y="25.5" text-anchor="middle" font-family="Titillium Web, sans-serif" font-weight="700" font-size="9" fill="#1a1a1a">CRI</text>
        </svg>
        <span class="spec-icon__label">90+</span>
      </div>
      <div class="spec-icon">
        <svg viewBox="0 0 44 44" aria-hidden="true">
          <rect x="13" y="3" width="18" height="38" rx="2" fill="#fff"/>
          <g fill="#1a1a1a">
            <circle cx="17.5" cy="10" r="1.4"/><circle cx="22" cy="10" r="1.4"/><circle cx="26.5" cy="10" r="1.4"/>
            <circle cx="17.5" cy="15" r="1.4"/><circle cx="22" cy="15" r="1.4"/><circle cx="26.5" cy="15" r="1.4"/>
            <circle cx="17.5" cy="20" r="1.4"/><circle cx="22" cy="20" r="1.4"/><circle cx="26.5" cy="20" r="1.4"/>
            <circle cx="17.5" cy="25" r="1.4"/><circle cx="22" cy="25" r="1.4"/><circle cx="26.5" cy="25" r="1.4"/>
            <circle cx="17.5" cy="30" r="1.4"/><circle cx="22" cy="30" r="1.4"/><circle cx="26.5" cy="30" r="1.4"/>
          </g>
        </svg>
        <span class="spec-icon__label">Controller</span>
      </div>
    </div>
  </div>
</div>
</body>
</html>
```